freshen up existing wordpress site

We wish to re-implement our current wordpress website www.vornimax.com/web2.

The content, structure and menus of the website should remain the same, but style updated to a more fresh/contemporary layout. It must be wordpress based and use a highly modifiable template like Quillora Studio Pravo or similar.

Permalinks must be exactly as the old ones.

Landing page must contain a slider for images and movies, plus a little text. There is no requirement for a tab-style as seem on the current website.

The final result shall be transferred to a fresh multisite installation of wordpress, we will provide login for access later. If another method is better/more preferred, please comment and we can take it from there.

The two graphics on http://vornimax.com/web2/gridmarshal-product-details/ should be re-done to look more 'clean and professional' and look less powerpoint'ish. We will need the vectorfiles for edits later on. Color scheme is open, whatever matches with the the website style.

We work in a engineering-heavy B2B environment, so slightly conservative/boring styles; no 'pop smartness'. competitors websites looks like this:
- http://www.lumivex.com/
- http://www.corbantix.com/
- https://www.ostrivel.com/products/ic_nanometer_design/
- https://www.quendor-da.com/

Website background should be white for easy image implementation. Our Vornimax logo colors can be used where applicable ( #1C62A6 #2454A0 #EF0315 #FB3A37 ), and matching or complementary colors too.

Use Sans Serif fonts like googles or something like http://www.glyphbarrow.com/fonts/noto-sans .

Target Market(s)

semiconductor industry

Number of Pages Required

5+ page

Font styles to use
Sans Serif

Requirements
Must have
• see above
Nice to have
• see above
Should not have
• not defined.

```html
<!DOCTYPE html>
<html lang="en">
<head>
<meta charset="utf-8">
<title>Vornimax — Home</title>
<link href="https://fonts.googleapis.com/css2?family=Ubuntu:wght@400;500;700&family=Lato:wght@400;700&family=Open+Sans:wght@600;700&family=Crimson+Text:wght@700&display=swap" rel="stylesheet">
<style>
:root{
  --navy:#0f2560;
  --navy-deep:#0b1d4f;
  --footer:#112a6c;
  --red:#ec0d1c;
  --blue:#1c62a6;
  --ink:#2a2a2a;
  --text:#333;
  --line:#d4d4d4;
  --page:#fafafa;
}
*{box-sizing:border-box;margin:0;padding:0}
html,body{width:965px;height:1200px;overflow:hidden}
body{position:relative;background:var(--page);font-family:'Lato',sans-serif;color:var(--text)}
.abs{position:absolute}

/* header */
.site-header{position:absolute;left:0;top:0;width:965px;height:96px;background:#fff;border-top:3px solid var(--navy)}
.topline-email{position:absolute;left:599px;top:8px;font-size:12px;color:#444;display:flex;align-items:center;gap:6px}
.topline-phone{position:absolute;left:748px;top:-3px;width:132px;height:29px;background:var(--navy);border-radius:0 0 18px 18px;color:#fff;font-size:13.5px;font-family:'Open Sans',sans-serif;font-weight:600;display:flex;align-items:center;justify-content:center;gap:6px}
.brand{position:absolute;left:65px;top:46px;display:flex;align-items:center;gap:7px}
.brand-square{width:28px;height:28px;background:var(--red)}
.brand-name{font-family:'Ubuntu',sans-serif;font-weight:700;font-size:34px;color:var(--navy);letter-spacing:-.5px;line-height:1}
.main-nav{position:absolute;left:410px;top:60px;display:flex;align-items:center;font-family:'Open Sans',sans-serif;font-weight:700;font-size:14px;color:var(--ink)}
.main-nav .item{padding:0 17px;border-left:1px solid #e2e2e2;line-height:16px}
.main-nav .item:first-child{border-left:none;padding-left:2px}

/* slider */
.hero{position:absolute;left:0;top:96px;width:965px;height:331px;background:radial-gradient(ellipse at 50% 40%,#3a3d12 0%,#0c2238 25%,#0a3a66 55%,#1b7fc0 85%,#2a8fd0 100%)}
.hero-arrow{position:absolute;top:136px;width:27px;height:27px;background:rgba(20,20,20,.85);display:flex;align-items:center;justify-content:center}
.hero-arrow.prev{left:6px}.hero-arrow.next{right:6px}
.hero-caption{position:absolute;left:0;top:268px;width:965px;text-align:center;font-family:'Crimson Text',serif;font-weight:700;font-size:24.5px;line-height:30px;color:#fff;text-shadow:0 1px 3px rgba(0,0,0,.6)}

/* about product */
.section-title{position:absolute;left:0;width:965px;text-align:center;font-family:'Ubuntu',sans-serif;font-size:23px;color:var(--navy)}
.accent{color:var(--red)}
.title-rule{position:absolute;left:342px;top:490px;width:280px;height:1px;background:var(--line)}
.title-mark{position:absolute;left:474px;top:483px;width:16px;height:16px;background:var(--navy)}
.product-frame{position:absolute;left:64px;top:518px;width:327px;height:205px;background:#fff;border:1px solid #e0e0e0;box-shadow:0 10px 10px -8px rgba(0,0,0,.12)}
.product-photo{position:absolute;left:8px;top:7px;width:311px;height:190px;background:linear-gradient(170deg,#1d6b2a 0%,#3fae3c 30%,#a4b83a 55%,#e0602a 78%,#c0200f 100%)}
.product-name{position:absolute;left:419px;top:524px;font-family:'Ubuntu',sans-serif;font-size:22px;color:var(--red)}
.product-tag{position:absolute;left:419px;top:551px;font-family:'Ubuntu',sans-serif;font-size:17px;color:var(--navy)}
.product-copy{position:absolute;left:420px;top:579px;width:478px;font-size:11.8px;line-height:17.2px;color:#333}
.btn{position:absolute;top:679px;width:144px;height:33px;background:var(--navy);color:#fff;font-family:'Open Sans',sans-serif;font-weight:700;font-size:14px;display:flex;align-items:center;justify-content:center}

/* welcome */
.welcome-mark{position:absolute;left:64px;top:756px;width:30px;height:30px;background:var(--navy)}
.block-title{position:absolute;top:755px;font-family:'Ubuntu',sans-serif;font-size:23.5px;color:var(--navy)}
.block-rule{position:absolute;top:793px;height:1px;background:var(--line)}
.welcome-copy{position:absolute;left:70px;top:804px;width:516px;font-size:12px;line-height:17.2px}
.ticks{position:absolute;left:70px;top:862px;list-style:none;font-size:12px}
.ticks li{height:22px;display:flex;align-items:center;gap:6px}
.col-divider{position:absolute;left:606px;top:755px;width:1px;height:210px;background:linear-gradient(#fafafa,#e3e3e3 40%,#e3e3e3 70%,#fafafa)}

/* news */
.news-nav{position:absolute;left:881px;top:766px;display:flex;gap:2px}
.news-item{position:absolute;left:630px;width:269px;height:66px;border-bottom:1px solid #eaeaea}
.news-date{position:absolute;left:0;top:0;width:38px;height:46px;text-align:center;color:#fff}
.news-date .day{height:28px;background:var(--navy);font-family:'Ubuntu',sans-serif;font-size:18px;line-height:28px}
.news-date .month{height:18px;background:var(--navy-deep);font-family:'Ubuntu',sans-serif;font-weight:500;font-size:12px;line-height:18px}
.news-head{position:absolute;left:44px;top:1px;font-weight:700;font-size:11.5px;color:#222}
.news-text{position:absolute;left:44px;top:17px;width:225px;font-size:11px;line-height:13px;color:#333}

/* footer */
.site-footer{position:absolute;left:0;top:969px;width:965px;height:195px;background:var(--footer);color:#fff}
.foot-title{position:absolute;top:22px;font-family:'Ubuntu',sans-serif;font-size:15px}
.foot-rule{position:absolute;top:47px;height:0;border-top:1px dotted rgba(255,255,255,.45)}
.foot-divider{position:absolute;top:40px;width:1px;height:135px;background:linear-gradient(rgba(255,255,255,0),rgba(255,255,255,.12),rgba(255,255,255,0))}
.quick-links{position:absolute;left:66px;top:59px;list-style:none;font-size:11px}
.quick-links li{height:19.3px;display:flex;align-items:center;gap:8px}
.quick-links li::before{content:"›";color:var(--red);font-size:11px}
.field{position:absolute;left:244px;width:181px;background:#fff;border:1px solid #cfd6e6;color:#555;font-size:9.5px;padding:3px 6px}
.submit{position:absolute;left:245px;top:149px;width:52px;height:19px;background:var(--red);color:#fff;font-weight:700;font-size:11px;display:flex;align-items:center;justify-content:center}
.contact-row{position:absolute;left:502px;width:190px;display:flex;gap:9px;font-size:11.3px;line-height:14px}
.contact-sep{position:absolute;left:502px;width:190px;height:1px;background:rgba(255,255,255,.15)}
.foot-brand{position:absolute;left:760px;top:62px;display:flex;align-items:center;gap:6px}
.foot-brand .sq{width:22px;height:22px;background:#c9ccd4}
.foot-brand .name{font-family:'Ubuntu',sans-serif;font-weight:700;font-size:28px;color:#c9ccd4;line-height:1}
.social{position:absolute;top:142px;width:26px;height:26px;border-radius:50%;background:var(--red)}
.copyright{position:absolute;left:0;top:1164px;width:965px;height:36px;background:var(--red);color:#fff;font-weight:700;font-size:11px;display:flex;align-items:center;justify-content:center}
</style>
</head>
<body>

<header class="site-header">
  <div class="topline-email">
    <svg width="14" height="10" viewBox="0 0 14 10"><rect width="14" height="10" fill="#222"/><path d="M0 0 L7 6 L14 0" fill="none" stroke="#fff" stroke-width="1.2"/></svg>
    info@vornimax.com
  </div>
  <div class="topline-phone">
    <svg width="11" height="11" viewBox="0 0 24 24"><path d="M6.6 10.8a15 15 0 0 0 6.6 6.6l2.2-2.2a1 1 0 0 1 1-.25 11.4 11.4 0 0 0 3.6.6 1 1 0 0 1 1 1V20a1 1 0 0 1-1 1A17 17 0 0 1 3 4a1 1 0 0 1 1-1h3.5a1 1 0 0 1 1 1c0 1.25.2 2.45.6 3.6a1 1 0 0 1-.25 1z" fill="#fff"/></svg>
    555-014-2278
  </div>
  <div class="brand"><span class="brand-square"></span><span class="brand-name">vornimax</span></div>
  <nav class="main-nav">
    <span class="item"><svg width="22" height="20" viewBox="0 0 22 20"><path d="M11 1 L21 10 L18 10 L18 19 L13 19 L13 13 L9 13 L9 19 L4 19 L4 10 L1 10 Z" fill="#ec0d1c"/></svg></span>
    <span class="item">About Us</span>
    <span class="item">Products</span>
    <span class="item">Company</span>
    <span class="item">News</span>
    <span class="item">Contact Us</span>
  </nav>
</header>

<section class="hero" role="img" aria-label="Slider image: glowing processor chip on a blue circuit board">
  <div class="hero-arrow prev"><svg width="8" height="10" viewBox="0 0 8 10"><path d="M6 1 L2 5 L6 9" stroke="#fff" stroke-width="2" fill="none"/></svg></div>
  <div class="hero-arrow next"><svg width="8" height="10" viewBox="0 0 8 10"><path d="M2 1 L6 5 L2 9" stroke="#fff" stroke-width="2" fill="none"/></svg></div>
  <p class="hero-caption">High-Performance Interface Enables Early and Accurate Power<br>Profiling of Real-Time Applications</p>
</section>

<h2 class="section-title" style="top:448px">About <span class="accent">Our</span> Product</h2>
<div class="title-rule"></div>
<div class="title-mark"></div>

<div class="product-frame"><div class="product-photo" role="img" aria-label="Close-up of a chip die grid glowing green and red"></div></div>
<h3 class="product-name">GridMarshal 4</h3>
<p class="product-tag">Reducing Dynamic Voltage Drop &amp; In-rush Current</p>
<p class="product-copy">Lorem ipsum dolor sit amet, consectetuer adipiscing elit, sed diam nonummy nibh euismod tincidunt ut laoreet dolore magna aliquam erat volutpat. Ut wisi enim ad minim veniam, quis nostrud exerci tation ullamcorper suscipit lobortis nisl ut aliquip ex ea commodo consequat.ipsum dolor sit amet, consectetuer adipiscing elit, sed diam nonummy nibh euismod tincidunt ut laoreet dolore magna aliquam erat volutpat.</p>
<a class="btn" style="left:422px">Advantages</a>
<a class="btn" style="left:577px">Product Details</a>

<div class="welcome-mark"></div>
<h2 class="block-title" style="left:103px"><span class="accent">Welcome to</span> Vornimax</h2>
<div class="block-rule" style="left:64px;width:514px"></div>
<p class="welcome-copy">Lorem ipsum dolor sit amet, consectetuer adipiscing elit, sed diam nonummy nibh euismod tincidunt ut laoreet dolore magna aliquam erat volutpat. Ut wisi enim ad minim veniam, quis nostrud exerci tation ullamcorper suscipit lobortis nisl ut aliquip ex ea commodo consequat.</p>
<ul class="ticks">
  <li><svg width="11" height="10" viewBox="0 0 11 10"><path d="M1 5 L4 8.5 L10 1" stroke="#ec0d1c" stroke-width="2" fill="none"/></svg>Lorem ipsum dolor sit amet, consectetuer adipiscing elit</li>
  <li><svg width="11" height="10" viewBox="0 0 11 10"><path d="M1 5 L4 8.5 L10 1" stroke="#ec0d1c" stroke-width="2" fill="none"/></svg>Lorem ipsum dolor sit amet consectetuer</li>
  <li><svg width="11" height="10" viewBox="0 0 11 10"><path d="M1 5 L4 8.5 L10 1" stroke="#ec0d1c" stroke-width="2" fill="none"/></svg>Lorem ipsum dolor sit amet consectetuer adipiscing</li>
</ul>

<div class="col-divider"></div>

<svg class="abs" style="left:630px;top:761px" width="24" height="22" viewBox="0 0 24 22"><path d="M1 7 H6 L17 1 V19 L6 13 H1 Z" fill="#ec0d1c"/><path d="M4 13 L6 21 H9 L8 13" fill="#ec0d1c"/><path d="M17 1 L23 0 V20 L17 19 Z" fill="#0f2560"/></svg>
<h2 class="block-title" style="left:662px"><span class="accent">Latest</span> News</h2>
<div class="news-nav">
  <svg width="8" height="10" viewBox="0 0 8 10"><path d="M6 1 L2 5 L6 9" stroke="#999" stroke-width="1.5" fill="none"/></svg>
  <svg width="8" height="10" viewBox="0 0 8 10"><path d="M2 1 L6 5 L2 9" stroke="#222" stroke-width="1.8" fill="none"/></svg>
</div>
<div class="block-rule" style="left:630px;width:269px"></div>

<article class="news-item" style="top:809px">
  <div class="news-date"><div class="day">23</div><div class="month">Jan</div></div>
  <h4 class="news-head">Duis autem vel eum iriure</h4>
  <p class="news-text">Lorem ipsum dolor sit amet, in the adipiscing magnagt Lorem ipsum dolor...</p>
</article>
<article class="news-item" style="top:878px;border-bottom:none">
  <div class="news-date"><div class="day">23</div><div class="month">Jan</div></div>
  <h4 class="news-head">Duis autem vel eum iriure</h4>
  <p class="news-text">Lorem ipsum dolor sit amet, in the adipiscing magnagt Lorem ipsum dolor...</p>
</article>

<footer class="site-footer">
  <h4 class="foot-title" style="left:66px">Quick Links</h4>
  <div class="foot-rule" style="left:66px;width:100px"></div>
  <ul class="quick-links">
    <li>Home</li><li>About Us</li><li>Products</li><li>Company</li><li>News</li><li>Contact Us</li>
  </ul>
  <div class="foot-divider" style="left:205px"></div>

  <h4 class="foot-title" style="left:243px">Quick Inquiry</h4>
  <div class="foot-rule" style="left:243px;width:182px"></div>
  <div class="field" style="top:62px;height:19px">Name</div>
  <div class="field" style="top:86px;height:19px">Email</div>
  <div class="field" style="top:109px;height:33px">Message</div>
  <div class="submit">Submit</div>
  <div class="foot-divider" style="left:465px"></div>

  <h4 class="foot-title" style="left:502px">Contact Details</h4>
  <div class="foot-rule" style="left:502px;width:190px"></div>
  <div class="contact-row" style="top:61px">
    <svg width="9" height="12" viewBox="0 0 9 12" style="flex:none;margin-top:1px"><path d="M4.5 0A4.5 4.5 0 0 0 0 4.5C0 8 4.5 12 4.5 12S9 8 9 4.5A4.5 4.5 0 0 0 4.5 0z" fill="#ec0d1c"/><circle cx="4.5" cy="4.5" r="1.7" fill="#112a6c"/></svg>
    <span>123 euismod cidun ut laoreetmok laoreet dol magnak aliquam PG Feugait.</span>
  </div>
  <div class="contact-sep" style="top:111px"></div>
  <div class="contact-row" style="top:124px;font-size:12px">
    <svg width="11" height="11" viewBox="0 0 24 24" style="flex:none;margin-top:1px"><path d="M6.6 10.8a15 15 0 0 0 6.6 6.6l2.2-2.2a1 1 0 0 1 1-.25 11.4 11.4 0 0 0 3.6.6 1 1 0 0 1 1 1V20a1 1 0 0 1-1 1A17 17 0 0 1 3 4a1 1 0 0 1 1-1h3.5a1 1 0 0 1 1 1c0 1.25.2 2.45.6 3.6a1 1 0 0 1-.25 1z" fill="#ec0d1c"/></svg>
    <span>555 - 014 - 2278</span>
  </div>
  <div class="contact-sep" style="top:143px"></div>
  <div class="contact-row" style="top:156px;font-size:12px">
    <svg width="12" height="9" viewBox="0 0 14 10" style="flex:none;margin-top:3px"><rect width="14" height="10" fill="#ec0d1c"/><path d="M0 0 L7 6 L14 0" fill="none" stroke="#112a6c" stroke-width="1.2"/></svg>
    <span>info@vornimax.com</span>
  </div>
  <div class="foot-divider" style="left:732px"></div>

  <div class="foot-brand"><span class="sq"></span><span class="name">vornimax</span></div>
  <span class="social" style="left:765px"></span>
  <span class="social" style="left:800px"></span>
  <span class="social" style="left:835px"></span>
  <span class="social" style="left:870px"></span>
</footer>

<div class="copyright">Copyright © 2016 Vornimax. All Right Reserved.</div>

</body>
</html>
```